RTavenor Business Cards & Letterhead

I have a logo but need a design for some new business cards. We are a Design-Build Firm that specializes in the design and construction of commercial projects.
the cards need to be professional. no cartoon stuff.
i would like to have the cards in AI format so I can update the card as needed. Logo is provided.
Our Address is: 4187 Marlowe Ct. Ashbury Vale, Easton County 27614

```html
<!DOCTYPE html>
<html lang="en">
<head>
<meta charset="utf-8">
<title>RTavenor Business Cards</title>
<link href="https://fonts.googleapis.com/css2?family=Montserrat:wght@500;700&family=Open+Sans:wght@400;600&display=swap" rel="stylesheet">
<style>
  :root {
    --backdrop: #4a4a49;
    --card: #141414;
    --card-deep: #0b0b0b;
    --accent: #1565c0;
    --accent-text: #1f7ccc;
    --ink: #ffffff;
    --muted: #6e6e6e;
  }
  * { margin: 0; padding: 0; box-sizing: border-box; }
  html, body {
    width: 1200px; height: 801px; overflow: hidden;
    background: var(--backdrop);
  }
  .stage {
    position: relative; width: 1200px; height: 801px;
    display: flex; align-items: center; justify-content: center; gap: 44px;
  }
  .card {
    position: relative; width: 520px; height: 298px;
    background: var(--card);
    border-radius: 14px;
    border-bottom: 3px solid var(--accent);
    border-right: 2px solid var(--accent);
    overflow: hidden;
    box-shadow: 0 18px 30px rgba(0,0,0,.35);
  }
  .brand {
    font-family: "Montserrat", sans-serif; font-weight: 700;
    letter-spacing: 1px; line-height: 1;
    display: flex; align-items: center; gap: 8px;
  }
  .brand-square { width: 22px; height: 22px; background: var(--accent); }
  .card-front .brand {
    position: absolute; left: 30px; top: 30px;
    font-size: 34px; color: var(--ink);
  }
  .edge-tab {
    position: absolute; left: 0; top: 118px;
    width: 16px; height: 34px; background: var(--accent);
  }
  .person { position: absolute; left: 30px; top: 98px; }
  .person-name {
    font-family: "Montserrat", sans-serif; font-weight: 700;
    font-size: 19px; color: var(--accent-text); letter-spacing: .5px;
  }
  .person-role {
    font-family: "Open Sans", sans-serif; font-size: 13px; color: var(--ink);
    margin-top: 2px;
  }
  .contact {
    position: absolute; left: 30px; top: 168px;
    list-style: none;
    font-family: "Open Sans", sans-serif; font-size: 13px; color: var(--ink);
  }
  .contact li { display: flex; align-items: center; gap: 8px; line-height: 20px; }
  .contact svg { width: 12px; height: 12px; fill: var(--accent-text); flex: none; }
  .address {
    position: absolute; left: 30px; top: 240px;
    font-family: "Open Sans", sans-serif; font-size: 13px; line-height: 18px;
    color: var(--ink); font-style: normal;
  }
  .emblem-area {
    position: absolute; right: 28px; top: 34px;
    width: 190px; height: 220px; border-radius: 30px;
    background: linear-gradient(135deg, #2a2a2a 0%, #101010 55%, #070707 100%);
  }
  .card-back { background: var(--card-deep); }
  .pattern-area {
    position: absolute; inset: 0;
    background: linear-gradient(140deg, #262626 0%, #141414 50%, #0c0c0c 100%);
  }
  .card-back .brand {
    position: absolute; left: 50%; top: 50%;
    transform: translate(-50%, -50%);
    font-size: 44px; color: var(--muted);
  }
  .card-back .brand-square { width: 28px; height: 28px; }
</style>
</head>
<body>
<main class="stage">
  <section class="card card-front">
    <div class="brand"><span class="brand-square"></span>RTAVENOR</div>
    <span class="edge-tab"></span>
    <div class="person">
      <p class="person-name">MARCUS HALE</p>
      <p class="person-role">Managing Director</p>
    </div>
    <ul class="contact">
      <li><svg viewBox="0 0 24 24"><path d="M6.6 10.8a15 15 0 0 0 6.6 6.6l2.2-2.2c.3-.3.7-.4 1-.2 1.1.4 2.3.6 3.6.6.6 0 1 .4 1 1V20c0 .6-.4 1-1 1A17 17 0 0 1 3 4c0-.6.4-1 1-1h3.5c.6 0 1 .4 1 1 0 1.3.2 2.5.6 3.6.1.3 0 .7-.2 1z"/></svg>919 555 0148</li>
      <li><svg viewBox="0 0 24 24"><path d="M2 5h20v14H2zm2 2v.4l8 5 8-5V7z"/></svg>info@rtavenorbuild.com</li>
      <li><svg viewBox="0 0 24 24"><circle cx="12" cy="12" r="10"/></svg>www.rtavenorbuild.com</li>
    </ul>
    <address class="address">4187 Marlowe Ct. Ashbury Vale,<br>Easton County 27614</address>
    <div class="emblem-area" role="img" aria-label="Large glossy brand emblem decoration"></div>
  </section>

  <section class="card card-back">
    <div class="pattern-area" role="img" aria-label="Embossed repeating brand emblem pattern"></div>
    <div class="brand"><span class="brand-square"></span>RTAVENOR</div>
  </section>
</main>
</body>
</html>
```